Business Card Design for Occupational Medicine Start Up Company

We need to design a professional business card. We are a healthcare company providing occupational medicine services to blue collar industries. We are professional, efficient and high quality service providers.

Target Market(s)

Blue Collar Industry: Shipbuilding, Ports, Trucking Companies; The Executives and Safety Officers for these companies

Industry/Entity Type

Healthcare

Contact Information for Business Card

Logo, Name, Title, Email, Phone

Other font styles liked:
• Please match our Brand Guide

Requirements
Must have
• Our Company Colors and Logo

```html
<!DOCTYPE html>
<html lang="en">
<head>
<meta charset="utf-8">
<title>CrewWell Business Card</title>
<link href="https://fonts.googleapis.com/css2?family=Source+Sans+3:wght@400;600&display=swap" rel="stylesheet">
<style>
  :root {
    --backdrop: #b0b2b1;
    --paper: #ffffff;
    --card-dark: #2a2a2b;
    --navy: #283583;
    --orange: #f2a93b;
    --sky: #3aa0dc;
    --ink: #4d4d4f;
    --muted: #6d6e71;
  }
  * { box-sizing: border-box; margin: 0; padding: 0; }
  html, body {
    width: 1200px; height: 1200px; overflow: hidden;
    background: var(--backdrop);
    font-family: "Source Sans 3", "Myriad Pro", sans-serif;
  }
  .card {
    position: absolute; left: 222px; width: 756px; height: 463px;
  }
  .card-front { top: 109px; background: var(--paper); }
  .card-back { top: 630px; background: var(--card-dark); }

  .brand-mark {
    position: absolute; border-radius: 50%;
  }
  .card-front .brand-mark {
    left: 160px; top: 62px; width: 76px; height: 76px; background: var(--navy);
  }
  .brand-name {
    position: absolute; font-weight: 600; white-space: nowrap; line-height: 1;
  }
  .card-front .brand-name {
    left: 47px; top: 160px; font-size: 42px; letter-spacing: 2px; color: var(--navy);
  }

  .person { position: absolute; right: 50px; top: 210px; text-align: right; }
  .person-name { font-size: 40px; font-weight: 600; color: var(--navy); line-height: 1.05; }
  .person-title { font-size: 23px; font-weight: 400; color: var(--muted); line-height: 1.1; }

  .rule {
    position: absolute; left: 47px; top: 275px; width: 467px; height: 2px; background: var(--orange);
  }

  .contact-list { position: absolute; left: 47px; top: 302px; list-style: none; }
  .contact-list li {
    display: flex; align-items: center; height: 31px;
    font-size: 22px; color: var(--ink);
  }
  .contact-list svg { width: 20px; height: 20px; margin-right: 10px; fill: var(--navy); flex: none; }

  .address { position: absolute; right: 50px; top: 330px; text-align: right; }
  .address svg { width: 20px; height: 26px; fill: var(--navy); margin-right: 2px; }
  .address p { font-size: 22px; color: var(--ink); line-height: 27px; }

  .card-back .brand-mark {
    left: 303px; top: 121px; width: 150px; height: 150px; background: var(--orange);
  }
  .card-back .brand-name {
    left: 0; width: 100%; text-align: center; top: 305px;
    font-size: 64px; letter-spacing: 5px; color: #ffffff;
  }
</style>
</head>
<body>
  <section class="card card-front">
    <span class="brand-mark"></span>
    <div class="brand-name">CREWWELL</div>

    <div class="person">
      <div class="person-name">Dana Reyes</div>
      <div class="person-title">Account Executive</div>
    </div>
    <div class="rule"></div>

    <ul class="contact-list">
      <li>
        <svg viewBox="0 0 24 24"><path d="M6.6 10.8a15.1 15.1 0 0 0 6.6 6.6l2.2-2.2a1 1 0 0 1 1-.25 11.4 11.4 0 0 0 3.6.57 1 1 0 0 1 1 1V20a1 1 0 0 1-1 1A17 17 0 0 1 3 4a1 1 0 0 1 1-1h3.5a1 1 0 0 1 1 1c0 1.25.2 2.45.57 3.57a1 1 0 0 1-.25 1z"/></svg>
        415.555.0142
      </li>
      <li>
        <svg viewBox="0 0 24 24"><path d="M6 2h12v5H6zM4 8h16a2 2 0 0 1 2 2v7h-4v5H6v-5H2v-7a2 2 0 0 1 2-2zm4 8v4h8v-4zm-1-5v1h3v-1z"/></svg>
        415.555.0187
      </li>
      <li>
        <svg viewBox="0 0 24 24"><path d="M2 4h18v7.5a6 6 0 0 0-8 6.5H2zm1.5 1.5v.4l7.5 5.6 7.5-5.6v-.4zM18 13a5 5 0 1 1 0 10 5 5 0 0 1 0-10zm-2.3 5 1.6 1.6 3-3-.8-.8-2.2 2.2-.8-.8z"/></svg>
        dreyes@crewwellhealth.com
      </li>
      <li>
        <svg viewBox="0 0 24 24"><path d="M12 2a10 10 0 1 0 0 20 10 10 0 0 0 0-20zm7.9 9h-3.9a15 15 0 0 0-1.4-6.6A8 8 0 0 1 19.9 11zM12 4c.9 1.2 1.8 3.7 2 7h-4c.2-3.3 1.1-5.8 2-7zM9.4 4.4A15 15 0 0 0 8 11H4.1a8 8 0 0 1 5.3-6.6zM4.1 13H8a15 15 0 0 0 1.4 6.6A8 8 0 0 1 4.1 13zM12 20c-.9-1.2-1.8-3.7-2-7h4c-.2 3.3-1.1 5.8-2 7zm2.6-.4A15 15 0 0 0 16 13h3.9a8 8 0 0 1-5.3 6.6z"/></svg>
        www.crewwellhealth.com
      </li>
    </ul>

    <div class="address">
      <svg viewBox="0 0 20 26"><path d="M10 0a10 10 0 0 0-10 10c0 7 10 16 10 16s10-9 10-16A10 10 0 0 0 10 0zm0 14a4 4 0 1 1 0-8 4 4 0 0 1 0 8z"/></svg>
      <p>48 Dockside Avenue Suite 210</p>
      <p>San Francisco, CA 94107</p>
    </div>
  </section>

  <section class="card card-back">
    <span class="brand-mark"></span>
    <div class="brand-name">CREWWELL</div>
  </section>
</body>
</html>
```